I need a fresh looking, exciting and loaded design for Full service Restaurant

We need a web design for our restaurant, which offers full service Pakistani and Indian food in PA, USA. Design should be elegant, simplified so customers can navigate easily and order food online for catering as well as delivery. We need loads of pictures and room to grow. I already have a web address via vemrilo.com. It should include SSL and e-commerce for ordering food.
Be original and be creative and make it a fun site :)

```html
<!DOCTYPE html>
<html lang="en">
<head>
<meta charset="utf-8">
<title>Saffron Lane – Pakistani &amp; Indian Restaurant</title>
<link href="https://fonts.googleapis.com/css2?family=Roboto:ital,wght@0,300;0,400;0,500;1,400;1,500&family=Satisfy&display=swap" rel="stylesheet">
<style>
:root{
  --red:#c8191e;
  --ink:#222;
  --text:#555;
  --muted:#888;
  --cream:#f1ede6;
  --green:#2d5a12;
  --green-dark:#234a0c;
  --night:#1f2326;
  --white:#fff;
  --line:#d6d6d6;
}
*{box-sizing:border-box;margin:0;padding:0}
html,body{width:1200px;height:3125px;overflow:hidden}
body{font-family:'Roboto',Arial,sans-serif;color:var(--text);background:var(--white);position:relative}
.script{font-family:'Satisfy','Brush Script MT','Segoe Script',cursive;font-weight:400}
.hero,.services,.chefs,.gallery,.testimonials,.contact,.footer{position:absolute;left:0;width:1200px;overflow:hidden}

/* hero */
.hero{top:0;height:625px;background:radial-gradient(ellipse at 62% 48%,#c26a2a 0%,#8a3f1b 30%,#4a231a 60%,#2a1a1a 100%)}
.site-header{position:absolute;top:0;left:58px;width:1084px;height:104px;background:var(--white);z-index:2}
.brand{position:absolute;left:20px;top:28px;display:flex;align-items:center;gap:10px}
.brand-dot{width:34px;height:34px;border-radius:50%;background:var(--red);display:block}
.brand-name{font-size:24px;font-weight:500;color:var(--red)}
.location{position:absolute;right:18px;top:20px;font-size:12px;color:#444;display:flex;align-items:center;gap:8px}
.location span{color:var(--red)}
.location i{width:26px;height:26px;border-radius:50%;background:#3b5998;display:block}
.nav{position:absolute;right:18px;top:66px;display:flex;gap:40px;font-size:12px;color:#333}
.nav a{color:inherit;text-decoration:none;padding-bottom:8px}
.nav a.active{color:var(--red);border-bottom:2px solid var(--red)}
.hero-title-band{position:absolute;left:280px;top:256px;width:610px;height:68px;background:rgba(0,0,0,.35)}
.hero h1{position:absolute;left:0;width:1200px;top:256px;line-height:66px;text-align:center;font-size:46px;color:var(--white)}
.hero-sub{position:absolute;left:220px;width:760px;top:340px;text-align:center;font-size:15px;line-height:22px;color:#eee}
.btn{display:inline-flex;align-items:center;justify-content:center;gap:12px;background:var(--red);color:var(--white);font-size:15px;text-decoration:none}
.hero .btn{position:absolute;left:496px;top:416px;width:208px;height:48px}
.arrow{position:absolute;top:290px;width:16px;height:28px}
.dots{position:absolute;top:594px;left:574px;display:flex;gap:6px}
.dots i{width:12px;height:12px;border:2px solid var(--white);border-radius:50%;display:block}
.dots i.on{background:var(--white)}

/* headings */
.sec-title{text-align:center;font-size:44px;line-height:56px;color:var(--ink)}
.sec-title em{font-style:normal;color:var(--red)}
.sec-lead{text-align:center;font-size:15px;line-height:22px}

/* services */
.services{top:625px;height:421px}
.services .sec-title{margin-top:42px}
.services .sec-lead{margin-top:4px;color:#555}
.service-grid{display:flex;justify-content:space-between;width:1020px;margin:54px auto 0}
.service{width:240px;text-align:center}
.service svg{width:100px;height:100px}
.service h3{margin-top:10px;font-size:17px;font-weight:400;color:var(--red)}
.service p{margin-top:6px;font-size:13px;line-height:20px;color:#555}

/* chefs */
.chefs{top:1046px;height:575px;background:var(--cream)}
.chefs .sec-title{position:absolute;left:180px;top:72px;font-size:40px;color:var(--red);text-align:left}
.chef-avatar{position:absolute;left:186px;top:144px;width:100px;height:100px;border-radius:50%;background:linear-gradient(135deg,#d8d8d8,#8a8a8a);border:4px solid var(--white)}
.chef-name{position:absolute;left:298px;top:172px;font-size:20px;color:#333}
.chef-role{position:absolute;left:298px;top:202px;font-size:13px;font-style:italic;color:#777}
.chef-quote{position:absolute;left:126px;top:262px;width:420px;font-size:16px;line-height:24px;font-style:italic;font-weight:500;color:#333}
.chef-bio{position:absolute;left:126px;top:328px;width:420px;font-size:13.5px;line-height:23px;color:#777}
.chef-nav{position:absolute;left:120px;top:464px;display:flex;gap:24px}
.chef-photo{position:absolute;left:600px;top:0;width:600px;height:575px;background:linear-gradient(120deg,#f4f1ec 0%,#d9c8b4 40%,#6a5446 75%,#2f2723 100%)}

/* gallery */
.gallery{top:1621px;height:475px;background:radial-gradient(ellipse at 50% 40%,var(--green) 0%,var(--green-dark) 100%)}
.gallery .sec-title{margin-top:38px;color:var(--white)}
.gallery .sec-lead{margin-top:10px;width:640px;margin-left:auto;margin-right:auto;font-size:12.5px;line-height:20px;color:#e4eedd}
.gallery-strip{position:absolute;top:189px;left:0;width:1200px;height:184px;display:flex;gap:8px}
.gallery-item{flex:0 0 240px;height:184px}
.g1{background:linear-gradient(135deg,#7a5a3a,#c27a2e,#e9e3d3)}
.g2{background:linear-gradient(135deg,#3a2418,#8a3d1c,#5a3020)}
.g3{background:linear-gradient(135deg,#a9866a,#c8521f,#d9b27a)}
.g4{background:linear-gradient(135deg,#5a3d28,#d9a06a,#c24b2a)}
.g5{flex-basis:220px;background:linear-gradient(135deg,#efe9e0,#b8622a,#8a3d1c)}
.gallery-nav{position:absolute;top:398px;left:566px;display:flex;gap:30px}

/* testimonials */
.testimonials{top:2096px;height:454px}
.testimonials .sec-title{margin-top:44px}
.quote-card{position:absolute;width:326px;border:1px solid var(--line);background:var(--white);padding:22px 28px 16px 36px;font-size:13.5px;line-height:22px;font-style:italic;color:#555;text-align:justify}
.quote-card::before{content:"\201C";position:absolute;left:12px;top:4px;font-size:46px;color:#ccc;font-style:normal;font-family:Georgia,serif}
.quote-card::after{content:"";position:absolute;left:96px;bottom:-11px;width:20px;height:20px;background:var(--white);border-right:1px solid var(--line);border-bottom:1px solid var(--line);transform:rotate(45deg)}
.q1{left:80px;top:122px;height:134px}
.q2{left:438px;top:122px;height:200px}
.q3{left:798px;top:122px;height:134px}
.author{position:absolute;display:flex;align-items:center;gap:14px}
.author i{width:60px;height:60px;border-radius:50%;background:linear-gradient(135deg,#e0c8b0,#7a5a44);display:block}
.author b{display:block;font-weight:400;font-size:14px;color:var(--red)}
.author small{font-size:11px;color:#777}
.a1{left:152px;top:276px}
.a2{left:512px;top:338px}
.a3{left:870px;top:276px}

/* contact */
.contact{top:2550px;height:441px;background:linear-gradient(90deg,#2a2d2f 0%,var(--night) 50%,#2c2c2a 100%)}
.contact .sec-title{margin-top:40px;color:var(--white)}
.contact .sec-lead{margin-top:12px;width:640px;margin-left:auto;margin-right:auto;font-size:12.5px;line-height:20px;color:#ccc}
.field{position:absolute;height:36px;border:1px solid #8a8c8e;display:flex;align-items:center;gap:8px;padding-left:14px;font-size:12px;color:#ddd}
.field svg{width:12px;height:12px}
.f-name{left:220px;top:198px;width:242px}
.f-mail{left:480px;top:198px;width:242px}
.f-phone{left:740px;top:198px;width:242px}
.f-comment{left:220px;top:250px;width:762px;height:70px;align-items:flex-start;padding-top:12px}
.contact .btn{position:absolute;left:522px;top:338px;width:156px;height:42px;font-size:14px}

/* footer */
.footer{top:2991px;height:134px;background:var(--cream)}
.socials{position:absolute;left:72px;top:38px;display:flex;gap:24px}
.socials i{width:26px;height:26px;border:2px solid #333;border-radius:5px;display:block}
.copy{position:absolute;left:72px;top:102px;font-size:12px;color:#333}
.newsletter{position:absolute;left:696px;top:68px;font-size:19px;color:#222}
.news-input{position:absolute;left:878px;top:62px;width:246px;height:34px;border:1px solid var(--line);background:var(--white);font-size:11px;color:#999;padding:10px 12px}
.news-go{position:absolute;left:1092px;top:62px;width:32px;height:34px;background:var(--red);display:flex;align-items:center;justify-content:center}
</style>
</head>
<body>

<section class="hero">
  <div role="img" aria-label="Close-up of a bowl of paneer curry with peas, green chillies on the side" style="position:absolute;inset:0"></div>
  <header class="site-header">
    <div class="brand"><i class="brand-dot"></i><span class="brand-name">Saffron Lane</span></div>
    <div class="location">BASED IN <span>PHILADELPHIA, USA</span><i></i></div>
    <nav class="nav">
      <a class="active" href="#">HOME</a><a href="#">ABOUT US</a><a href="#">MENU</a><a href="#">RESERVATIONS</a><a href="#">BLOG</a><a href="#">CONTACTS</a>
    </nav>
  </header>
  <div class="hero-title-band"></div>
  <h1 class="script">We Offer Best Quality Food</h1>
  <p class="hero-sub">Fresh spices, slow cooked curries and hot tandoor breads made daily in our kitchen. Dine in, take away or order catering for your next family event.</p>
  <a class="btn" href="#"><svg width="22" height="14" viewBox="0 0 22 14"><path d="M1 7C5 1 17 1 21 7C17 13 5 13 1 7Z" fill="none" stroke="#fff" stroke-width="1.6"/><circle cx="11" cy="7" r="3" fill="none" stroke="#fff" stroke-width="1.6"/></svg>VIEW MORE</a>
  <svg class="arrow" style="left:8px" viewBox="0 0 16 28"><path d="M13 3L3 14L13 25" fill="none" stroke="#fff" stroke-width="2.5"/></svg>
  <svg class="arrow" style="right:8px" viewBox="0 0 16 28"><path d="M3 3L13 14L3 25" fill="none" stroke="#fff" stroke-width="2.5"/></svg>
  <div class="dots"><i class="on"></i><i></i><i></i></div>
</section>

<section class="services">
  <h2 class="sec-title script"><em>Our</em> Services</h2>
  <p class="sec-lead">We offer full service Pakistani and Indian food in Philadelphia, USA</p>
  <div class="service-grid">
    <div class="service">
      <svg viewBox="0 0 100 100" fill="none" stroke="#111" stroke-width="4" stroke-linecap="round"><path d="M42 10c-6 6 6 10 0 18M54 12c-6 6 6 10 0 18"/><path d="M22 44h50v14c0 16-11 26-25 26S22 74 22 58Z"/><path d="M72 50c12 0 12 16 0 16"/><path d="M14 90h70"/></svg>
      <h3>DRINKS &amp; SWEETS</h3>
      <p>Nulla semper arcu vel diam auctor condimentum. Nam molestie sem eu quam fermen aliquet.</p>
    </div>
    <div class="service">
      <svg viewBox="0 0 100 100" fill="none" stroke="#111" stroke-width="4" stroke-linejoin="round"><path d="M18 40L50 28L82 40L74 88H26Z"/><path d="M18 40L50 54L82 40M50 54V88"/><path d="M56 30L84 6M62 32L90 12"/></svg>
      <h3>LUNCH</h3>
      <p>Nulla semper arcu vel diam auctor condimentum. Nam molestie sem eu quam fermen aliquet.</p>
    </div>
    <div class="service">
      <svg viewBox="0 0 100 100" fill="none" stroke="#111" stroke-width="4" stroke-linecap="round"><path d="M44 8c-4 6 4 8 0 14M56 8c-4 6 4 8 0 14"/><path d="M28 52c4-18 40-18 44 0"/><path d="M32 44c10-4 26-4 36 0M36 38c8-3 20-3 28 0"/><ellipse cx="50" cy="62" rx="40" ry="12"/><path d="M22 74c10 8 46 8 56 0"/></svg>
      <h3>DINNER</h3>
      <p>Nulla semper arcu vel diam auctor condimentum. Nam molestie sem eu quam fermen aliquet.</p>
    </div>
    <div class="service">
      <svg viewBox="0 0 100 100" fill="none" stroke="#111" stroke-width="4" stroke-linecap="round"><circle cx="50" cy="52" r="26"/><circle cx="50" cy="52" r="17"/><path d="M10 14v22c0 6 8 6 8 0V14M14 36v54"/><path d="M86 14c-10 8-10 30 0 34v42"/></svg>
      <h3>CUSTOM</h3>
      <p>Nulla semper arcu vel diam auctor condimentum. Nam molestie sem eu quam fermen aliquet.</p>
    </div>
  </div>
</section>

<section class="chefs">
  <h2 class="sec-title script">About Our Chefs</h2>
  <div class="chef-avatar" role="img" aria-label="Portrait of the executive chef"></div>
  <div class="chef-name">Idris Malvane</div>
  <div class="chef-role">Executive Chef</div>
  <p class="chef-quote">Class aptent taciti sociosqu ad litora torquent per conubia nostra, per inceptos himenaeos.</p>
  <p class="chef-bio">Lorem ipsum dolor sit amet, consectetur adipiscing elit. Integer lorem quam, adipiscing condimentum tristique vel, eleifend sed turpis. Pellentesque cursus arcu id magna euismod in elementum purus molestie. Curabitur pellentesque massa eu nulla consequat sed porttitor arcu porttitor.</p>
  <div class="chef-nav">
    <svg width="14" height="22" viewBox="0 0 14 22"><path d="M11 2L3 11L11 20" fill="none" stroke="#888" stroke-width="2"/></svg>
    <svg width="14" height="22" viewBox="0 0 14 22"><path d="M3 2L11 11L3 20" fill="none" stroke="#888" stroke-width="2"/></svg>
  </div>
  <div class="chef-photo" role="img" aria-label="Chef in a white hat plating a dish"></div>
</section>

<section class="gallery">
  <h2 class="sec-title script">Our Gallery</h2>
  <p class="sec-lead">Aenean sodales dictum augue, in faucibus nisi sollicitudin eu. Nulla semper arcu vel diam auctor condimentum. Nam molestie sem eu quam fermentum a tempus nisi aliquet.</p>
  <div class="gallery-strip">
    <div class="gallery-item g1" role="img" aria-label="Curry served with rice"></div>
    <div class="gallery-item g2" role="img" aria-label="Grilled kebab skewers"></div>
    <div class="gallery-item g3" role="img" aria-label="Tandoori chicken with lemon"></div>
    <div class="gallery-item g4" role="img" aria-label="Bowl of biryani"></div>
    <div class="gallery-item g5" role="img" aria-label="Grilled chicken fillets"></div>
  </div>
  <div class="gallery-nav">
    <svg width="14" height="22" viewBox="0 0 14 22"><path d="M11 2L3 11L11 20" fill="none" stroke="#cfe0c4" stroke-width="2"/></svg>
    <svg width="14" height="22" viewBox="0 0 14 22"><path d="M3 2L11 11L3 20" fill="none" stroke="#cfe0c4" stroke-width="2"/></svg>
  </div>
</section>

<section class="testimonials">
  <h2 class="sec-title script"><em>Customer</em> Say's</h2>
  <blockquote class="quote-card q1">Lorem ipsum dolor sit amet, consecte adipiscing elit, sed do eiusmod tempor incidid ut labore et dolore magna aliqua. Lorem ipsum dolor amet consectetur.</blockquote>
  <blockquote class="quote-card q2">Lorem ipsum dolor sit amet, consecte adipiscing elit, sed do eiusmod tempor incidid ut labore et dolore magna aliqua. Lorem ipsum dolor amet consectetur. Lorem ipsum dolor sit amet, consecte adipiscing elit, sed do eiusmod tempor incidid ut labore et dolore.</blockquote>
  <blockquote class="quote-card q3">Lorem ipsum dolor sit amet, consecte adipiscing elit, sed do eiusmod tempor incidid ut labore et dolore magna aliqua. Lorem ipsum dolor amet consectetur.</blockquote>
  <div class="author a1"><i role="img" aria-label="Customer portrait"></i><div><b>By Author Name</b><small>City Location</small></div></div>
  <div class="author a2"><i role="img" aria-label="Customer portrait"></i><div><b>By Author Name</b><small>City Location</small></div></div>
  <div class="author a3"><i role="img" aria-label="Customer portrait"></i><div><b>By Author Name</b><small>City Location</small></div></div>
</section>

<section class="contact">
  <div role="img" aria-label="Dim restaurant dining room with chairs" style="position:absolute;inset:0"></div>
  <h2 class="sec-title script" style="position:relative">Quick Contact</h2>
  <p class="sec-lead" style="position:relative">Aenean sodales dictum augue, in faucibus nisi sollicitudin eu. Nulla semper arcu vel diam auctor condimentum. Nam molestie sem eu quam fermentum a tempus nisi aliquet.</p>
  <div class="field f-name"><svg viewBox="0 0 12 12"><circle cx="6" cy="3.5" r="2.6" fill="#ddd"/><path d="M1 12c0-4 10-4 10 0Z" fill="#ddd"/></svg>Enter Name</div>
  <div class="field f-mail"><svg viewBox="0 0 12 12"><rect x="0.8" y="2" width="10.4" height="8" fill="none" stroke="#ddd"/><path d="M1 2.5L6 7L11 2.5" fill="none" stroke="#ddd"/></svg>Enter Email</div>
  <div class="field f-phone"><svg viewBox="0 0 12 12"><path d="M2 1h2.5l1 3-1.5 1c.6 1.4 1.6 2.4 3 3l1-1.5 3 1V11C5 11 1 7 1 2Z" fill="#ddd"/></svg>Enter Phone</div>
  <div class="field f-comment"><svg viewBox="0 0 12 12"><path d="M1 2h10v6H5l-3 3V8H1Z" fill="#ddd"/></svg>Leave Comment</div>
  <a class="btn" href="#">SUBMIT</a>
</section>

<footer class="footer">
  <div class="socials"><i></i><i></i><i></i><i></i></div>
  <p class="copy">© 2015 Saffron Lane. All Rights Reserved</p>
  <div class="newsletter">Newsletter Sign Up</div>
  <div class="news-input">Enter Email</div>
  <div class="news-go"><svg width="10" height="12" viewBox="0 0 10 12"><path d="M2 1L8 6L2 11" fill="none" stroke="#fff" stroke-width="2"/></svg></div>
</footer>

</body>
</html>
```